Wandering Rooms Stationary Set

Wandering Rooms is a bespoke interior design firm set to provide services to VIP clients with elegance and minimalism is the main theme for our stationary set. We require a full stationary set covering A4 letterhead, A4 & A3 envelopes, business cards, USB's, CDs, email signature and any other item the designer sees fit. logo is already designed and finalized, and we require the designer to use it as is without modifying the logo.

Address to be used on letterhead / business cards ...etc shall be as follows:

Phone : +971 2 518 2047
P.O. Box : 309186
Address: Block C&D, Bldg. 47, Court 12, Abu Dhabi, United Arab Emirates
Website: www.wanderingrooms-example.com

Target Market(s)

VIP Clients

Industry/Entity Type

Interior Design

Font styles to use
Other font styles liked:
• something to be unique

Colors

Designer to choose colors to be used in the design.

Requirements
Must have
• Elegant, minimalistic
Nice to have
• Simple yet elegant design having a sharp yet clean cut format
Should not have
• No additional colours, just colours that are used in the logo (silver, black or gold)

```html
<!DOCTYPE html>
<html lang="en">
<head>
<meta charset="utf-8">
<title>Wandering Rooms – Business Card</title>
<link rel="stylesheet" href="https://fonts.googleapis.com/css2?family=Allura&family=EB+Garamond:wght@400;500&display=swap">
<style>
  :root {
    --backdrop: #1b1b1b;
    --card: #262626;
    --card-edge: #2e2e2e;
    --silver: #9a9a9a;
    --gold: #b89a5c;
    --gold-light: #c8ab6c;
    --ink: #1e1e1e;
    --white: #ececec;
  }
  * { box-sizing: border-box; margin: 0; padding: 0; }
  html, body {
    width: 1200px; height: 800px; overflow: hidden;
    background: var(--backdrop);
    font-family: "EB Garamond", Georgia, serif;
  }
  .canvas { position: relative; width: 1200px; height: 800px; }
  .card {
    position: absolute; left: 320px;
    width: 560px; height: 320px;
    background: var(--card);
    border: 1px solid var(--card-edge);
    box-shadow: 0 10px 24px rgba(0,0,0,.45);
    overflow: hidden;
  }
  .card--front { top: 60px; }
  .card--back { top: 420px; }

  .wordmark {
    position: absolute; inset: 0;
    display: flex; align-items: center; justify-content: center;
  }
  .wordmark__name {
    font-family: "EB Garamond", Georgia, serif;
    font-weight: 400; font-size: 44px; letter-spacing: 6px;
    color: var(--silver);
    text-transform: uppercase;
  }

  .back__pattern { position: absolute; inset: 0; }
  .band {
    position: absolute; left: 0; right: 0; top: 150px; height: 96px;
    background: linear-gradient(90deg,
      rgba(184,154,92,0) 0%, var(--gold) 14%, var(--gold-light) 50%,
      var(--gold) 86%, rgba(184,154,92,0) 100%);
  }
  .holder {
    position: absolute; left: 200px; top: 104px;
    display: flex; align-items: baseline; gap: 8px;
  }
  .holder__name { font-family: "Allura", cursive; font-size: 30px; color: var(--gold-light); }
  .holder__divider { width: 1px; height: 18px; background: var(--white); align-self: center; }
  .holder__role { font-size: 17px; color: var(--white); }

  .contact {
    position: absolute; right: 36px; top: 158px;
    list-style: none; font-size: 12.5px; color: var(--ink);
  }
  .contact__item { display: flex; align-items: center; gap: 8px; line-height: 18px; }
  .contact__icon { width: 11px; height: 11px; fill: var(--ink); flex: none; }

  .address {
    position: absolute; left: 56px; top: 194px;
    font-size: 12.5px; line-height: 16px; color: var(--ink); font-style: normal;
  }
</style>
</head>
<body>
<main class="canvas">

  <section class="card card--front" aria-label="Business card front">
    <div class="wordmark">
      <span class="wordmark__name">Wandering Rooms</span>
    </div>
  </section>

  <section class="card card--back" aria-label="Business card back">
    <svg class="back__pattern" width="560" height="320" role="img" aria-label="Faint repeated wordmark pattern on the card background">
      <rect x="280" y="0" width="280" height="320" fill="#2a2a2a" opacity="0.6"/>
    </svg>

    <div class="band"></div>

    <div class="holder">
      <span class="holder__name">Daniel Hale</span>
      <span class="holder__divider"></span>
      <span class="holder__role">President</span>
    </div>

    <ul class="contact">
      <li class="contact__item">
        <svg class="contact__icon" viewBox="0 0 24 24"><path d="M6.6 10.8a15.1 15.1 0 0 0 6.6 6.6l2.2-2.2a1 1 0 0 1 1-.25 11.4 11.4 0 0 0 3.6.57 1 1 0 0 1 1 1V20a1 1 0 0 1-1 1A17 17 0 0 1 3 4a1 1 0 0 1 1-1h3.5a1 1 0 0 1 1 1c0 1.25.2 2.45.57 3.57a1 1 0 0 1-.25 1z"/></svg>
        +971 2 518 2047
      </li>
      <li class="contact__item">
        <svg class="contact__icon" viewBox="0 0 24 24"><path d="M2 5h20v14H2z M3.5 6.5 12 13l8.5-6.5" fill="var(--ink)"/><path d="M3.5 6.5 12 13l8.5-6.5" fill="none" stroke="#b89a5c" stroke-width="1.6"/></svg>
        info@wanderingrooms-example.com
      </li>
      <li class="contact__item">
        <svg class="contact__icon" viewBox="0 0 24 24"><circle cx="12" cy="12" r="10"/><path d="M2 12h20M12 2c3 3 3 17 0 20M12 2c-3 3-3 17 0 20" fill="none" stroke="#b89a5c" stroke-width="1.4"/></svg>
        www.wanderingrooms-example.com
      </li>
    </ul>

    <address class="address">
      P.O. Box : 309186,<br>
      Block C&amp;D, Bldg. 47, Court 12<br>
      Abu Dhabi, United Arab Emirates
    </address>
  </section>

</main>
</body>
</html>
```